MRT Property - Business Cards

Looking for a business card & general letterhead, signage etc design for our new logo.

Colours:
000a20
0056a2
00b5ef
0088ce
68cef2

Fonts:
Poppins
Karla

Please keep look and feel of new brand - example in the zip package I sent.

```html
<!DOCTYPE html>
<html lang="en">
<head>
<meta charset="utf-8">
<title>MRT Property – Business Cards</title>
<link rel="stylesheet" href="https://fonts.googleapis.com/css2?family=Poppins:wght@400;600;700&family=Karla:wght@400;500&display=swap">
<style>
  :root {
    --ink-navy: #000a20;
    --card-navy: #1b2038;
    --brand-blue: #0056a2;
    --deep-blue: #0a3266;
    --bright-blue: #0088ce;
    --sky-blue: #00b5ef;
    --pale-blue: #68cef2;
    --paper: #f6f7f8;
    --text-dark: #2b2f3a;
    --stage: #1e1f22;
  }
  * { margin: 0; padding: 0; box-sizing: border-box; }
  html, body {
    width: 1200px; height: 852px; overflow: hidden;
    background: var(--stage);
    font-family: "Karla", sans-serif;
  }
  .sheet {
    position: relative; width: 1200px; height: 852px;
    display: flex; align-items: center; justify-content: center; gap: 40px;
  }
  .card {
    position: relative; width: 540px; height: 310px;
    border-radius: 16px; overflow: hidden;
  }

  /* Front */
  .card--front {
    background: linear-gradient(135deg, #22284a 0%, var(--card-navy) 55%, #141830 100%);
  }
  .wordmark {
    font-family: "Poppins", sans-serif; font-weight: 700;
    letter-spacing: 0.5px; white-space: nowrap;
  }
  .card--front .wordmark {
    position: absolute; left: 50%; top: 112px; transform: translateX(-50%);
    font-size: 44px; color: var(--brand-blue);
    display: flex; align-items: center; gap: 14px;
  }
  .wordmark__dot {
    width: 18px; height: 18px; background: currentColor; flex: none;
  }
  .front-url {
    position: absolute; right: 30px; bottom: 30px;
    font-family: "Karla", sans-serif; font-size: 12px;
    letter-spacing: 6px; color: #c8ccd8;
  }
  .front-rule {
    position: absolute; left: 0; right: 0; bottom: 14px; height: 5px;
    display: flex;
  }
  .front-rule__dark { flex: 3; background: var(--brand-blue); }
  .front-rule__light { flex: 2; background: var(--bright-blue); }

  /* Back */
  .card--back { background: var(--paper); }
  .back-panel { position: absolute; inset: 0; width: 540px; height: 310px; }
  .card--back .wordmark {
    position: absolute; left: 34px; top: 168px;
    font-size: 30px; color: #ffffff;
    display: flex; align-items: center; gap: 10px;
  }
  .card--back .wordmark__dot { width: 12px; height: 12px; }
  .contact {
    position: absolute; left: 318px; top: 62px; color: var(--text-dark);
  }
  .contact__name {
    font-family: "Poppins", sans-serif; font-weight: 600;
    font-size: 20px; color: var(--bright-blue); line-height: 1.1;
  }
  .contact__role {
    font-family: "Poppins", sans-serif; font-size: 10px;
    color: var(--text-dark); margin-top: 2px;
  }
  .contact__list { list-style: none; margin-top: 26px; }
  .contact__item {
    display: flex; align-items: center; gap: 10px;
    font-family: "Poppins", sans-serif; font-size: 11.5px; line-height: 20px;
  }
  .contact__icon { width: 12px; height: 12px; flex: none; fill: var(--text-dark); }
  .contact__item--address { padding-left: 22px; }
</style>
</head>
<body>
<main class="sheet">

  <section class="card card--front" aria-label="Business card front">
    <div class="wordmark"><span class="wordmark__dot"></span>MRT Property</div>
    <p class="front-url">www.mrtproperty.com</p>
    <div class="front-rule"><span class="front-rule__dark"></span><span class="front-rule__light"></span></div>
  </section>

  <section class="card card--back" aria-label="Business card back">
    <svg class="back-panel" viewBox="0 0 540 310" aria-hidden="true">
      <path d="M0 0 H210 Q300 140 262 310 H0 Z" fill="var(--bright-blue)"/>
      <path d="M0 0 H200 Q288 140 250 310 H0 Z" fill="var(--deep-blue)"/>
    </svg>
    <div class="wordmark"><span class="wordmark__dot"></span>MRT Property</div>

    <div class="contact">
      <h1 class="contact__name">Daniel Hoskins</h1>
      <p class="contact__role">Associate Director</p>
      <ul class="contact__list">
        <li class="contact__item">
          <svg class="contact__icon" viewBox="0 0 24 24"><path d="M6.6 10.8a15 15 0 0 0 6.6 6.6l2.2-2.2c.3-.3.7-.4 1-.2 1.1.4 2.3.6 3.6.6.6 0 1 .4 1 1V20c0 .6-.4 1-1 1A17 17 0 0 1 3 4c0-.6.4-1 1-1h3.5c.6 0 1 .4 1 1 0 1.3.2 2.5.6 3.6.1.3 0 .7-.2 1z"/></svg>
          555-014-2290
        </li>
        <li class="contact__item">
          <svg class="contact__icon" viewBox="0 0 24 24"><path d="M2 5h20v14H2z M2 5l10 8 10-8" stroke="#f6f7f8" stroke-width="1.5"/></svg>
          daniel@mrtproperty.com
        </li>
        <li class="contact__item">
          <svg class="contact__icon" viewBox="0 0 24 24"><circle cx="12" cy="12" r="10"/><path d="M2 12h20M12 2c3 3 3 17 0 20M12 2c-3 3-3 17 0 20" stroke="#f6f7f8" stroke-width="1.3" fill="none"/></svg>
          www.mrtproperty.com
        </li>
        <li class="contact__item contact__item--address">52 Harbour View Road Northside</li>
      </ul>
    </div>
  </section>

</main>
</body>
</html>
```